Moravel Aesthetic Doctor

I require an elegant, luxurious looking business card for my aesthetic business. I am a doctor and that will set me aside from competitors. I am planning to provide home and spa based treatments to clients with high expectations. I have attached my logo.

```html
<!DOCTYPE html>
<html lang="en">
<head>
<meta charset="utf-8">
<title>Moravel Aesthetic Doctor – Business Card</title>
<link href="https://fonts.googleapis.com/css2?family=Montserrat:wght@300;400;500&display=swap" rel="stylesheet">
<style>
  :root {
    --stage: #3a3a3c;
    --card: #232325;
    --sky: #55b4e8;
    --silver: #a9b1be;
    --white: #f4f6f8;
  }
  * { box-sizing: border-box; margin: 0; padding: 0; }
  html, body { width: 799px; height: 1200px; overflow: hidden; }
  body {
    background: var(--stage);
    font-family: "Montserrat", sans-serif;
    position: relative;
  }
  .card {
    position: absolute;
    left: 70px;
    width: 660px;
    height: 377px;
    background: var(--card);
    border-radius: 4px;
    overflow: hidden;
    box-shadow: 0 10px 28px rgba(0,0,0,.45);
  }
  .card--front { top: 110px; }
  .card--back { top: 700px; }

  .brand {
    position: absolute;
    display: flex;
    align-items: center;
    gap: 16px;
  }
  .brand__mark {
    width: 74px; height: 74px;
    border: 3px solid var(--silver);
    border-radius: 50%;
  }
  .brand__name {
    color: var(--silver);
    font-weight: 300;
    text-transform: uppercase;
    line-height: 1.05;
  }
  .brand__name span { display: block; }
  .brand__name .brand__main { font-size: 44px; letter-spacing: 4px; }
  .brand__name .brand__sub { font-size: 19px; letter-spacing: 3px; }

  .card--front .brand { left: 150px; top: 50px; }

  .services {
    position: absolute;
    left: 0; right: 0; top: 185px;
    text-align: center;
    color: var(--white);
    font-size: 17px;
    line-height: 1.45;
  }
  .band {
    position: absolute;
    left: 0; right: 0; top: 262px;
    height: 44px;
    background: var(--sky);
    color: var(--white);
    font-size: 18px;
    letter-spacing: 1px;
    text-align: center;
    line-height: 44px;
  }

  .wave { position: absolute; inset: 0; }
  .card--back .brand { left: 40px; top: 62px; }
  .brand--back .brand__mark { width: 66px; height: 66px; }
  .brand--back .brand__main { font-size: 40px; }
  .brand--back .brand__sub { font-size: 17px; }

  .doctor {
    position: absolute;
    left: 40px; top: 160px;
  }
  .doctor__name { color: var(--silver); font-size: 22px; font-weight: 300; }
  .doctor__post { color: var(--sky); font-size: 11px; margin-top: 2px; }
  .doctor__cred { color: var(--sky); font-size: 15px; line-height: 1.25; margin-top: 6px; }

  .tagline {
    position: absolute;
    right: 34px; top: 150px;
    color: var(--white);
    font-size: 17px;
    text-align: right;
    line-height: 1.3;
  }

  .contact {
    position: absolute;
    right: 34px; bottom: 26px;
    list-style: none;
    text-align: right;
    color: var(--silver);
    font-size: 16px;
  }
  .contact li {
    display: flex;
    justify-content: flex-end;
    align-items: center;
    gap: 8px;
    line-height: 27px;
  }
  .contact svg { width: 16px; height: 16px; fill: var(--sky); }
  .social-dot {
    width: 14px; height: 14px; border-radius: 50%;
    background: var(--sky); display: inline-block;
  }
</style>
</head>
<body>

<section class="card card--front">
  <div class="brand">
    <div class="brand__mark"></div>
    <div class="brand__name">
      <span class="brand__main">Moravel</span>
      <span class="brand__sub">Aesthetic Doctor</span>
    </div>
  </div>
  <p class="services">
    Dermal Injectables &nbsp;|&nbsp; Plasma Facials &nbsp;|&nbsp; Microneedling<br>
    Skin Boosters &nbsp;|&nbsp; Excessive Sweating
  </p>
  <div class="band">HOME AND SPA BASED TREATMENTS</div>
</section>

<section class="card card--back">
  <svg class="wave" viewBox="0 0 660 377" aria-hidden="true">
    <path d="M200,0 L660,0 L660,200 C570,190 490,150 430,100 C360,40 290,12 200,0 Z" fill="#55b4e8"/>
    <path d="M150,22 C270,20 350,70 420,130 C500,200 580,236 660,236" fill="none" stroke="#a9b1be" stroke-width="8"/>
  </svg>

  <div class="brand brand--back">
    <div class="brand__mark"></div>
    <div class="brand__name">
      <span class="brand__main">Moravel</span>
      <span class="brand__sub">Aesthetic Doctor</span>
    </div>
  </div>

  <div class="doctor">
    <p class="doctor__name">Dr Elin Varga</p>
    <p class="doctor__post">MRCPCH MD</p>
    <p class="doctor__cred">Australasian Diploma of<br>Aesthetic Medicine</p>
  </div>

  <p class="tagline">Home and Spa<br>Based Treatments</p>

  <ul class="contact">
    <li>Follow us on: <span class="social-dot"></span><span class="social-dot"></span></li>
    <li>0800 555 014
      <svg viewBox="0 0 24 24"><path d="M6.6 10.8a15 15 0 0 0 6.6 6.6l2.2-2.2a1 1 0 0 1 1-.25 11.4 11.4 0 0 0 3.6.57 1 1 0 0 1 1 1V20a1 1 0 0 1-1 1A17 17 0 0 1 3 4a1 1 0 0 1 1-1h3.5a1 1 0 0 1 1 1c0 1.25.2 2.45.57 3.57a1 1 0 0 1-.25 1z"/></svg>
    </li>
    <li>elin@moravel.co.nz
      <svg viewBox="0 0 24 24"><path d="M2 5h20v14H2z M3 6l9 7 9-7" fill="none" stroke="#55b4e8" stroke-width="2"/></svg>
    </li>
    <li>www.moravel.co.nz
      <svg viewBox="0 0 24 24"><g fill="none" stroke="#55b4e8" stroke-width="2"><circle cx="12" cy="12" r="9"/><ellipse cx="12" cy="12" rx="4" ry="9"/><path d="M3 12h18"/></g></svg>
    </li>
  </ul>
</section>

</body>
</html>
```